Sales sheet for printing and embroidery apparel items - Copper Hollow Graphics

I would like a one page flyer or sales sheet that I would use as a template to send different images of apparel we produce. I have attached examples of layouts I like.
- Ideally, it would have space for 3-5 items.
- I would like it one page only - not a folding flyer.
- Our companies name is Copper Hollow Graphics.
- This will be used for many different products and markets so I don't need wording/copy. You can use wording from the 7M9 or T58 flyer.

Colors
0054AA
0677BA
7BADD7
CADEEF
E8F1F8
00AB8E
00BBA5
67D7C9
C6EFE9
E9F9F6
FFC000
F8CF3A
FAE287
FDF2CF
FEFAEE

Requirements
Must have
• Places for between 3 and 5 images of apparel (t-shirts, hats etc)

```html
<!DOCTYPE html>
<html lang="en">
<head>
<meta charset="utf-8">
<title>Copper Hollow Graphics – Sales Sheet</title>
<link href="https://fonts.googleapis.com/css2?family=Exo+2:ital,wght@1,800;1,900&family=Roboto:wght@400;500&family=Roboto+Condensed:wght@700&display=swap" rel="stylesheet">
<style>
:root{
  --blue:#0054AA;
  --blue-mid:#0677BA;
  --blue-soft:#CADEEF;
  --blue-pale:#E8F1F8;
  --teal:#00AB8E;
  --teal-bright:#00BBA5;
  --teal-soft:#C6EFE9;
  --yellow:#FFC000;
  --yellow-soft:#FDF2CF;
  --white:#ffffff;
  --ink:#14213a;
  --pasteboard:#b0b0b0;
  --photo-gold:#e0a22a;
  --photo-blue:#2f8fc0;
}
*{margin:0;padding:0;box-sizing:border-box}
html,body{width:906px;height:1200px;overflow:hidden;background:var(--pasteboard)}
.canvas{position:relative;width:906px;height:1200px}
.sheet{position:absolute;left:53px;top:0;width:800px;height:1200px;background:var(--white);overflow:hidden;font-family:"Roboto",sans-serif}
.abs{position:absolute}
.display{font-family:"Exo 2",sans-serif;font-style:italic;font-weight:900;text-transform:uppercase;white-space:nowrap}

/* hero */
.hero-photo{left:0;top:0}
.brand{left:455px;top:18px;width:240px;display:flex;flex-direction:column;align-items:center;gap:10px}
.brand-mark{width:54px;height:54px;background:var(--blue)}
.brand-name{font-family:"Exo 2",sans-serif;font-style:italic;font-weight:900;font-size:17px;color:var(--blue);text-transform:uppercase;white-space:nowrap}
.headline{left:390px;top:132px}
.headline span{display:block;line-height:.88}
.headline .l1{font-size:52px;color:var(--teal)}
.headline .l2{font-size:56px;color:var(--blue)}
.headline .l3{font-size:42px;color:var(--blue)}

/* features band */
.feature-band{left:0;top:280px;width:800px;height:155px;background:var(--teal);border-radius:0 0 78px 78px}
.feature{position:absolute;top:8px;width:160px;text-align:center;color:var(--white)}
.feature svg{display:block;margin:0 auto;height:68px}
.feature-title{font-family:"Exo 2",sans-serif;font-style:italic;font-weight:800;font-size:17px;text-transform:uppercase;margin-top:12px;white-space:nowrap}
.feature-text{font-size:10.8px;line-height:13.5px;margin-top:2px}

/* section headings */
.section-title{left:0;width:800px;text-align:center;font-size:30px}
.rule{position:absolute;left:360px;width:80px;height:2px;background:var(--yellow)}

/* products */
.products-title{top:458px;color:var(--blue)}
.product-slot{top:516px;width:143px;height:152px;background:var(--blue-pale);border-radius:2px}

/* offer + order bands */
.order-band{left:0;top:790px;width:800px;height:310px;background:var(--blue);border-radius:0 0 78px 78px}
.offer-band{left:0;top:689px;width:800px;height:177px;background:var(--teal);border-radius:88px}
.offer-title{top:719px;color:var(--white)}
.offer-item{position:absolute;top:788px;height:46px;display:flex;align-items:center;gap:8px;color:var(--white);font-weight:500;font-size:13.5px;line-height:16px;white-space:nowrap}
.offer-divider{position:absolute;top:780px;width:1px;height:62px;background:rgba(255,255,255,.4)}

.order-title{top:895px;color:var(--white)}
.step{position:absolute;top:948px;width:212px;text-align:center;color:var(--white)}
.step svg{display:block;margin:0 auto;height:44px}
.step-title{font-family:"Exo 2",sans-serif;font-style:italic;font-weight:800;font-size:17px;text-transform:uppercase;margin-top:8px;white-space:nowrap}
.step-text{font-size:12.5px;line-height:15px;margin-top:3px}
.step-arrow{position:absolute;top:1002px}

/* contact */
.closing{left:27px;top:1118px;font-family:"Roboto Condensed",sans-serif;font-weight:700;font-size:30px;color:var(--blue);text-transform:uppercase;white-space:nowrap}
.contact{top:1158px;display:flex;align-items:center;gap:8px;white-space:nowrap}
.contact-icon{width:26px;height:26px;border-radius:50%;background:var(--teal);display:flex;align-items:center;justify-content:center;flex:none}
.phone{left:19px;font-family:"Roboto Condensed",sans-serif;font-weight:700;font-size:22px;color:var(--ink)}
.email{left:200px;font-size:15px;color:var(--ink)}
.badge{position:absolute;top:1128px;height:28px}
.social{position:absolute;top:1167px;width:18px;height:18px;border-radius:50%;background:var(--teal)}
</style>
</head>
<body>
<div class="canvas">
<main class="sheet">

  <!-- hero -->
  <svg class="abs hero-photo" width="370" height="282" viewBox="0 0 370 282">
    <defs>
      <linearGradient id="photoTone" x1="0" y1="0" x2="1" y2="1">
        <stop offset="0" stop-color="#d9b98e"/>
        <stop offset=".35" stop-color="#2f8fc0"/>
        <stop offset=".6" stop-color="#e0a22a"/>
        <stop offset="1" stop-color="#c9821c"/>
      </linearGradient>
      <linearGradient id="arcTone" x1="0" y1="0" x2="0" y2="1">
        <stop offset="0" stop-color="#0054AA"/>
        <stop offset="1" stop-color="#00AB8E"/>
      </linearGradient>
    </defs>
    <path d="M250 0 A151 151 0 0 1 250 280" fill="none" stroke="url(#arcTone)" stroke-width="4" transform="translate(7 0)"/>
    <path role="img" aria-label="Close-up photo of an embroidery machine stitching a colourful patch" d="M0 0 H250 A151 151 0 0 1 250 280 H0 Z" fill="url(#photoTone)"/>
  </svg>

  <div class="abs brand">
    <span class="brand-mark"></span>
    <span class="brand-name">Copper Hollow Graphics</span>
  </div>

  <h1 class="abs headline display">
    <span class="l1">Order Shirts</span>
    <span class="l2">For Your All</span>
    <span class="l3">Of Your Retreats</span>
  </h1>

  <!-- features -->
  <section class="abs feature-band">
    <div class="feature" style="left:25px">
      <svg viewBox="0 0 70 70" fill="none" stroke="#fff" stroke-width="1.6"><path d="M14 40 L36 62 L62 36 L40 14 L30 12 L14 28 Z"/><path d="M14 44 L36 66 L62 40"/><path d="M14 48 L36 70 L62 44"/><path d="M30 12 Q36 22 44 18"/></svg>
      <div class="feature-title">Low Minimums</div>
      <div class="feature-text">Order as few as 24 pieces to get started.</div>
    </div>
    <div class="feature" style="left:228px">
      <svg viewBox="0 0 70 70" fill="none" stroke="#fff" stroke-width="1.6"><path d="M10 10 L20 12 L34 54 L64 44"/><rect x="30" y="18" width="22" height="22" transform="rotate(-18 41 29)"/><circle cx="34" cy="58" r="4"/><path d="M4 40 H18 M2 46 H20 M6 52 H22"/></svg>
      <div class="feature-title">Fast Turnaround</div>
      <div class="feature-text">2-week standard delivery.</div>
    </div>
    <div class="feature" style="left:431px">
      <svg viewBox="0 0 80 70" fill="none" stroke="#fff" stroke-width="1.6"><circle cx="40" cy="12" r="7"/><path d="M28 60 V32 Q28 24 40 24 Q52 24 52 32 V60 Z"/><circle cx="22" cy="14" r="5"/><circle cx="58" cy="14" r="5"/><path d="M14 52 V30 Q14 24 24 24 M66 52 V30 Q66 24 56 24"/><circle cx="8" cy="16" r="4"/><circle cx="72" cy="16" r="4"/></svg>
      <div class="feature-title">Real People</div>
      <div class="feature-text">Work with our team of experts and artists.</div>
    </div>
    <div class="feature" style="left:623px">
      <svg viewBox="0 0 80 70" fill="none" stroke="#fff" stroke-width="1.6"><path d="M40 6 L56 12 V28 Q56 40 40 46 Q24 40 24 28 V12 Z"/><circle cx="40" cy="26" r="8"/><path d="M36 26 L39 29 L45 22"/><path d="M8 50 Q20 44 34 50 H50 Q54 54 48 56 H36 M48 56 L66 48 Q72 48 68 54 L50 64 H20 L8 60"/><path d="M16 18 H10 M64 18 H70 M18 8 L14 4 M62 8 L66 4"/></svg>
      <div class="feature-title">Guaranteed</div>
      <div class="feature-text">We promise accurate, quality work.</div>
    </div>
  </section>

  <!-- products -->
  <h2 class="abs section-title display products-title">Our Products</h2>
  <span class="rule" style="top:495px"></span>
  <div class="abs product-slot" role="img" aria-label="Apparel product image" style="left:25px"></div>
  <div class="abs product-slot" role="img" aria-label="Apparel product image" style="left:176px"></div>
  <div class="abs product-slot" role="img" aria-label="Apparel product image" style="left:328px"></div>
  <div class="abs product-slot" role="img" aria-label="Apparel product image" style="left:479px"></div>
  <div class="abs product-slot" role="img" aria-label="Apparel product image" style="left:631px"></div>

  <!-- order band sits behind offer band -->
  <section class="abs order-band"></section>

  <section class="abs offer-band"></section>
  <h2 class="abs section-title display offer-title">We Offer</h2>
  <span class="rule" style="top:759px"></span>

  <div class="offer-item" style="left:23px">
    <svg width="50" height="50" viewBox="0 0 50 50" fill="#fff"><path d="M25 12 l3 0 1 4 4 2 3-3 3 3-3 3 2 4 4 1 0 4-4 1-2 4 3 3-3 3-3-3-4 2-1 4h-6l-1-4-4-2-3 3-3-3 3-3-2-4-4-1v-4l4-1 2-4-3-3 3-3 3 3 4-2 1-4z"/><circle cx="25" cy="30" r="6" fill="#00AB8E"/><rect x="23" y="2" width="4" height="22"/><rect x="16" y="6" width="3" height="16"/><rect x="31" y="6" width="3" height="16"/></svg>
    <span>Art Design</span>
  </div>
  <span class="offer-divider" style="left:158px"></span>
  <div class="offer-item" style="left:171px">
    <svg width="52" height="34" viewBox="0 0 52 34" fill="#fff"><rect x="1" y="2" width="32" height="22" rx="3"/><path d="M35 8 H44 L51 16 V26 H35 Z"/><circle cx="11" cy="28" r="5"/><circle cx="42" cy="28" r="5"/><text x="4" y="17" font-family="Exo 2,sans-serif" font-weight="900" font-style="italic" font-size="10" fill="#00AB8E">FREE</text></svg>
    <span>Free Shipping</span>
  </div>
  <span class="offer-divider" style="left:332px"></span>
  <div class="offer-item" style="left:357px">
    <svg width="40" height="44" viewBox="0 0 40 44" fill="#fff"><circle cx="24" cy="12" r="11"/><text x="19" y="17" font-family="Roboto,sans-serif" font-weight="500" font-size="14" fill="#00AB8E">$</text><rect x="2" y="28" width="6" height="14"/><path d="M10 30 Q18 26 26 30 H32 Q36 32 32 34 H22 M10 40 H28 L38 32"/></svg>
    <span>We Pay ALL Royalties<br>to the Movement</span>
  </div>
  <span class="offer-divider" style="left:553px"></span>
  <div class="offer-item" style="left:578px">
    <svg width="32" height="32" viewBox="0 0 32 32" fill="#fff"><path d="M10 2 L16 6 L22 2 L31 8 L27 15 L24 13 V31 H8 V13 L5 15 L1 8 Z"/><path d="M13 4 L16 12 L19 4" fill="#00AB8E"/></svg>
    <span style="margin-left:8px">Many Options of Shirt<br>Styles and Colors</span>
  </div>

  <!-- how to order -->
  <h2 class="abs section-title display order-title">How To Start An Order</h2>
  <span class="rule" style="top:934px"></span>

  <div class="step" style="left:24px">
    <svg viewBox="0 0 44 44" fill="none" stroke="#fff" stroke-width="1.6"><circle cx="18" cy="18" r="15"/><path d="M29 29 L40 40"/><path d="M8 21 V17 L12 12 H24 L28 17 V21 Z"/><circle cx="12" cy="21" r="2"/><circle cx="24" cy="21" r="2"/></svg>
    <div class="step-title">Choose Your Ride</div>
    <div class="step-text">Send us a picture, or let us know the make and model of the vehicle you would like featured on your apparel.</div>
  </div>
  <svg class="step-arrow" style="left:241px" width="44" height="10" viewBox="0 0 44 10" fill="none" stroke="#fff" stroke-width="1.3"><path d="M0 5 H42 M37 1 L42 5 L37 9"/></svg>
  <div class="step" style="left:298px">
    <svg viewBox="0 0 44 44" fill="none" stroke="#fff" stroke-width="1.6"><path d="M14 2 L22 6 L30 2 L42 8 L38 17 L34 15 V30 M10 30 V15 L6 17 L2 8 Z"/><path d="M20 40 L18 30 Q18 26 21 28 L23 32 V22 Q23 19 26 20 V28 L32 29 Q35 30 34 34 L32 42"/></svg>
    <div class="step-title">Pick Your Gear</div>
    <div class="step-text">We will help you choose your t-shirts, sweatshirts or other apparel items and determine sizes and quantities.</div>
  </div>
  <svg class="step-arrow" style="left:522px" width="44" height="10" viewBox="0 0 44 10" fill="none" stroke="#fff" stroke-width="1.3"><path d="M0 5 H42 M37 1 L42 5 L37 9"/></svg>
  <div class="step" style="left:572px">
    <svg viewBox="0 0 44 44" fill="none" stroke="#fff" stroke-width="1.8"><path d="M6 38 L30 14 M10 42 L34 18 M30 14 L38 6 L42 10 L34 18"/><path d="M6 8 Q10 2 16 6 L38 30 Q42 36 36 40 L14 18 Q4 16 6 8 Z"/></svg>
    <div class="step-title">We Customize</div>
    <div class="step-text">We make the magic happen and our team of expert artists will design your shirts and get a proof out to you. Upon order</div>
  </div>

  <!-- contact -->
  <p class="abs closing">We'd Love To Work With You!</p>
  <div class="abs contact phone">
    <span class="contact-icon"><svg width="14" height="14" viewBox="0 0 24 24" fill="#fff"><path d="M6.6 10.8a15.1 15.1 0 0 0 6.6 6.6l2.2-2.2a1 1 0 0 1 1-.25 11.4 11.4 0 0 0 3.6.57 1 1 0 0 1 1 1V20a1 1 0 0 1-1 1A17 17 0 0 1 3 4a1 1 0 0 1 1-1h3.5a1 1 0 0 1 1 1c0 1.25.2 2.45.57 3.570a1 1 0 0 1-.25 1z"/></svg></span>
    555-014-2287
  </div>
  <div class="abs contact email">
    <span class="contact-icon"><svg width="14" height="14" viewBox="0 0 24 24" fill="#fff"><path d="M6.6 10.8a15.1 15.1 0 0 0 6.6 6.6l2.2-2.2a1 1 0 0 1 1-.25 11.4 11.4 0 0 0 3.6.57 1 1 0 0 1 1 1V20a1 1 0 0 1-1 1A17 17 0 0 1 3 4a1 1 0 0 1 1-1h3.5a1 1 0 0 1 1 1c0 1.25.2 2.45.57 3.57a1 1 0 0 1-.25 1z"/></svg></span>
    hello@copperhollowtees.com
  </div>

  <span class="badge" style="left:468px;width:28px;border-radius:50%;background:var(--teal-soft)" role="img" aria-label="Certification badge"></span>
  <span class="badge" style="left:512px;width:28px;border-radius:50%;background:var(--yellow-soft)" role="img" aria-label="Certification badge"></span>
  <span class="badge" style="left:555px;width:76px;background:var(--blue-soft)" role="img" aria-label="Certification badge"></span>
  <span class="badge" style="left:641px;width:46px;border-radius:14px;background:var(--blue-pale)" role="img" aria-label="Listing badge"></span>
  <span class="badge" style="left:696px;width:38px;border-radius:14px;background:var(--teal-soft)" role="img" aria-label="Certification badge"></span>
  <span class="badge" style="left:744px;width:34px;border-radius:4px;background:var(--yellow-soft)" role="img" aria-label="Membership badge"></span>

  <span class="social" style="left:714px" role="img" aria-label="Social profile"></span>
  <span class="social" style="left:738px" role="img" aria-label="Social profile"></span>
  <span class="social" style="left:762px" role="img" aria-label="Social profile"></span>

</main>
</div>
</body>
</html>
```